Valdane Companies Business Card Design

We need a new business card for our Private Equity Real Estate Development firm, “Valdane” and our EB-5 regional center “Thornmere Regional Center” on one card. We prefer a design that is simple, elegant, and represents the luxury products we design and build as well as the financial security and stability our successful history has produced. We are an industry leader in our field and 3rd generation family business that has evolved into an institutional quality investment platform. Considered design size is standard business card dimensions (3.5 x 2 inches with an additional 1/8 inch space for design elements or backgrounds that extend beyond the finished size of your piece.

Target Market(s)

• High net worth individuals
• Highly skilled technical workers and physicians in the US seeking investment-based immigration opportunities
• Sophisticated private equity investors
• Intermediary partners include domestic attorneys and investment brokers, as well as international agent networks
• US real estate developers

Industry/Entity Type

Finance

Contact Information for Business Card

(Providing placeholder info for personal information, please design for longer character spaces, longer names and addresses etc..)
• Logo for Valdane
• Logo for Thornmere Regional Center
• Full name: Marcus Valdane
• Job title: CEO
• Email address: mvaldane@valdanecompanies.com
• Cell phone number: +1.555.314.2287
• Office number +1.555.628.4410
• Office address: Larkfield Court 5, 4817 Vista Orilla, San Ramon, CA.
• Website: www.valdanecompanies.com

Font styles to use
Serif
Sans Serif

Colors
ec1f27
ffffff
000000

Requirements
Must have
• • Logo for Valdane
• • Logo for Thornmere Regional Center
• - Use rounded corners
• (See .ai file included for logos)
Nice to have
• • Simple, elegant design
• • Aesthetically compatible with our website design (www.valdanecompanies.com)
• • Color palette including but not limited to white, black, and red (as per logos)
Should not have
• - Not too much red color
• - Do not stack both logos on top of each other

```html
<!DOCTYPE html>
<html lang="en">
<head>
<meta charset="utf-8">
<title>Valdane Companies Business Card</title>
<link href="https://fonts.googleapis.com/css2?family=Cinzel:wght@400;700&family=Source+Sans+3:wght@400;600&display=swap" rel="stylesheet">
<style>
  :root {
    --stage: #2a2a2a;
    --card-white: #ffffff;
    --card-black: #1a1a1a;
    --ink: #1c1c1c;
    --ink-soft: #555555;
    --rule: #c8c8c8;
    --mark: #3a3a3a;
    --silver: #d9d9d9;
    --pattern-a: #202020;
    --pattern-b: #262626;
  }
  * { box-sizing: border-box; margin: 0; padding: 0; }
  html, body { width: 1200px; height: 1108px; overflow: hidden; }
  body { background: var(--stage); position: relative; font-family: "Source Sans 3", sans-serif; }

  .card {
    position: absolute; top: 169px; width: 440px; height: 770px;
    border-radius: 28px; overflow: hidden;
  }
  .card--front { left: 130px; background: var(--card-white); color: var(--ink); text-align: center; }
  .card--back { left: 630px; background: var(--card-black); }

  .brand { position: absolute; top: 100px; left: 0; right: 0; }
  .brand__square { width: 84px; height: 84px; background: var(--mark); margin: 0 auto 22px; border-radius: 6px; }
  .brand__name { font-family: "Cinzel", serif; font-weight: 700; font-size: 58px; line-height: 1; letter-spacing: 1px; color: var(--ink); }
  .brand__sub { font-family: "Cinzel", serif; font-weight: 700; font-size: 17px; letter-spacing: 9px; margin-top: 8px; color: var(--ink); }

  .person { position: absolute; top: 400px; left: 60px; right: 60px; }
  .person__name { font-family: "Cinzel", serif; font-size: 31px; letter-spacing: 1px; }
  .person__title { font-size: 17px; margin-top: 2px; }
  .rule { height: 1px; background: var(--rule); margin: 14px 0; }

  .contact { list-style: none; font-size: 19px; line-height: 1.3; }
  .contact b { font-weight: 600; }
  .address { font-size: 19px; line-height: 1.3; }

  .pattern {
    position: absolute; inset: 0 0 180px 0;
    background: linear-gradient(160deg, var(--pattern-b), var(--pattern-a));
  }
  .center-logo {
    position: absolute; left: 44px; right: 30px; bottom: 78px;
    display: flex; align-items: center; gap: 18px;
  }
  .center-logo__square { width: 72px; height: 72px; background: var(--silver); border-radius: 5px; flex: none; }
  .center-logo__divider { width: 1px; height: 96px; background: var(--silver); flex: none; }
  .center-logo__name {
    font-family: "Cinzel", serif; font-weight: 700; color: var(--silver);
    font-size: 27px; line-height: 1.15; letter-spacing: 1px;
  }
</style>
</head>
<body>
  <section class="card card--front">
    <div class="brand">
      <div class="brand__square"></div>
      <div class="brand__name">VALDANE</div>
      <div class="brand__sub">CAPITAL</div>
    </div>
    <div class="person">
      <div class="person__name">MARCUS VALDANE</div>
      <div class="person__title">CEO</div>
      <div class="rule"></div>
      <ul class="contact">
        <li><b>P:</b> +1.555.314.2287</li>
        <li><b>M:</b> +1.555.628.4410</li>
        <li><b>E:</b> mvaldane@valdanecompanies.com</li>
        <li><b>W:</b> www.valdanecompanies.com</li>
      </ul>
      <div class="rule"></div>
      <p class="address">Larkfield Court 5, 4817 Vista<br>Orilla, San Ramon, CA</p>
    </div>
  </section>

  <section class="card card--back">
    <div class="pattern" role="img" aria-label="Faint repeated monogram pattern in dark grey"></div>
    <div class="center-logo">
      <div class="center-logo__square"></div>
      <div class="center-logo__divider"></div>
      <div class="center-logo__name">THORNMERE<br>REGIONAL CENTER</div>
    </div>
  </section>
</body>
</html>
```